Initial website for sport tech startup

We are currently in the R&D phases of our new product. It’s a headband to prevent concussion in the soccer market initially.

We have 2 products, one that’s basic aimed at the youth market and the other more technology driven that’s aimed at the academies and professional market.

Initially the product will launch in the UK

Target Market(s)

Youth soccer players and parents in UK, Soccer Clubs, Federations.

Industry/Entity Type

Sporting Good

Coding

Coded - Design and coding required

Number of Pages Required

5+ page

Requirements
Must have
• Professional style that can be adapted and changed over the coming months.
Nice to have
• Ecommerce ability in the future.

```html
<!DOCTYPE html>
<html lang="en">
<head>
<meta charset="utf-8">
<title>Helmora – Bringing Safety to the Sports Concussion Debate</title>
<link rel="stylesheet" href="https://fonts.googleapis.com/css2?family=Lato:wght@400;700;900&display=swap">
<style>
:root{
  --brand:#0f5a9a;
  --brand-dark:#0b4a82;
  --ink:#2a2a2a;
  --muted:#7d7d7d;
  --night:#070d18;
  --night-2:#10151d;
  --white:#ffffff;
  --rule:#1f6bb0;
}
*{box-sizing:border-box;margin:0;padding:0}
html,body{width:1200px;height:3790px;overflow:hidden}
body{font-family:'Lato',sans-serif;color:var(--ink);background:var(--white);position:relative}
.abs{position:absolute}

/* header */
.site-header{position:absolute;left:0;top:0;width:1200px;height:105px;background:var(--white)}
.wordmark{position:absolute;left:112px;top:20px;width:228px;height:54px;border:3px solid var(--brand);color:var(--brand);font-weight:700;font-size:36px;letter-spacing:1px;display:flex;align-items:center;justify-content:center}
.main-nav{position:absolute;left:412px;top:42px;display:flex;gap:31px;font-size:14px;color:#333}
.main-nav .active{color:var(--brand);border-bottom:3px solid var(--brand);padding-bottom:9px}
.quote-btn{position:absolute;left:905px;top:24px;width:183px;height:56px;border:3px solid var(--brand);color:var(--brand);font-size:14px;font-weight:700;display:flex;align-items:center;justify-content:center}

/* hero */
.hero{position:absolute;left:0;top:105px;width:1200px;height:515px;background:radial-gradient(ellipse at 60% 30%,#c99a5a 0%,#6f5a3a 35%,#2d2a22 70%),#2d2a22}
.hero::after{content:"";position:absolute;left:0;bottom:0;width:100%;height:150px;background:linear-gradient(to bottom,rgba(80,110,40,0),#6f8a3c)}
.hero-title{position:absolute;left:109px;top:158px;color:var(--white);font-weight:700;font-size:36px;line-height:51px;z-index:2}
.hero-arrow{position:absolute;top:220px;z-index:2}
.scroll-cue{position:absolute;left:0;width:1200px;text-align:center;top:420px;color:var(--white);font-size:11px;font-weight:700;z-index:2}
.scroll-line{position:absolute;left:600px;top:560px;width:1px;height:104px;background:#444;z-index:3}

/* about */
.about{position:absolute;left:112px;top:723px;width:976px;height:234px}
.about .frame-top-l{position:absolute;left:0;top:0;width:275px;height:3px;background:var(--rule)}
.about .frame-top-r{position:absolute;right:0;top:0;width:275px;height:3px;background:var(--rule)}
.about .frame-l{position:absolute;left:0;top:0;width:3px;height:234px;background:var(--rule)}
.about .frame-r{position:absolute;right:0;top:0;width:3px;height:234px;background:var(--rule)}
.about .frame-bot-l{position:absolute;left:0;bottom:0;width:332px;height:3px;background:var(--rule)}
.about .frame-bot-r{position:absolute;right:0;bottom:0;width:332px;height:3px;background:var(--rule)}
.about h2{position:absolute;left:0;width:100%;top:-16px;text-align:center;font-size:35px;font-weight:900;color:#222}
.about h2 span{color:var(--brand)}
.about p{position:absolute;left:55px;right:55px;top:66px;text-align:center;font-size:13px;line-height:26px;color:var(--muted)}
.btn{position:absolute;background:var(--brand);color:var(--white);font-size:14px;font-weight:700;display:flex;align-items:center;justify-content:center;gap:6px}
.btn-read{left:515px;top:928px;width:170px;height:53px}

/* mission / market */
.mission{position:absolute;left:0;top:1084px;width:598px;height:448px;background:linear-gradient(135deg,#0b1322,#03070f)}
.market{position:absolute;left:598px;top:1110px;width:602px;height:449px;background:linear-gradient(160deg,#1b5fa0,#0b4f8f)}
.panel h3{position:absolute;font-size:36px;font-weight:700;color:var(--white)}
.panel h4{position:absolute;font-size:16px;font-weight:900;color:var(--white);line-height:25px}
.panel p{position:absolute;font-size:13.5px;font-weight:700;color:var(--white);line-height:25.7px;text-align:justify}

/* targets */
.section-title{position:absolute;left:0;width:1200px;text-align:center;font-size:35px;font-weight:700;color:#222}
.target{position:absolute;top:1734px;width:309px;text-align:center}
.target .photo{width:309px;height:200px}
.target h5{font-size:21px;font-weight:400;margin-top:26px;color:#222}
.target .bar{width:34px;height:2px;background:var(--brand);margin:11px auto 13px}
.target p{font-size:13.5px;line-height:26px;color:var(--muted);padding:0 25px}
.t-arrow{position:absolute;top:1900px}

/* product */
.product{position:absolute;left:0;top:2147px;width:1200px;height:594px;background:linear-gradient(100deg,#090d14 0%,#14191f 55%,#262b31 100%)}
.product h3{position:absolute;left:109px;top:124px;font-size:36px;font-weight:700;color:var(--white)}
.product h4{position:absolute;left:111px;top:182px;width:440px;font-size:20px;font-weight:700;color:var(--white);line-height:28px}
.product p{position:absolute;left:111px;top:280px;width:420px;font-size:13.5px;line-height:25.8px;color:var(--white);text-align:justify}
.product .shot{position:absolute;left:596px;top:110px;width:472px;height:381px;background:var(--white)}
.product .shot .art{position:absolute;left:70px;top:90px;width:330px;height:200px;background:radial-gradient(ellipse,#5b6068 0%,#8a8e94 55%,#ffffff 75%)}

/* team */
.member{position:absolute;top:2920px;width:290px;text-align:center}
.member .avatar{width:146px;height:146px;border-radius:50%;margin:0 auto}
.member h5{font-size:19px;font-weight:400;margin-top:37px;color:#222}
.member .role{font-size:19px;color:var(--brand);margin-top:10px}
.member p{font-size:13.5px;line-height:25.7px;color:var(--muted);margin-top:10px;text-align:justify;text-align-last:center}

/* footer */
.footer{position:absolute;left:0;top:3428px;width:1200px;height:362px;background:linear-gradient(180deg,#0d0f12,#1c1e22)}
.footer .f-mark{position:absolute;left:112px;top:66px;width:215px;height:52px;border:3px solid var(--white);color:var(--white);font-weight:700;font-size:35px;display:flex;align-items:center;justify-content:center}
.footer .f-about{position:absolute;left:111px;top:134px;width:240px;font-size:13.5px;line-height:25.7px;color:var(--white)}
.footer h6{position:absolute;top:68px;font-size:19px;font-weight:700;color:var(--white)}
.footer h6::after{content:"";display:block;width:26px;height:2px;background:var(--white);margin-top:8px}
.footer ul{position:absolute;top:114px;list-style:none;font-size:13.5px;line-height:25.7px;color:var(--white)}
.footer .contact{position:absolute;left:659px;top:114px;font-size:13.5px;line-height:25.7px;color:var(--white);width:170px}
.footer .socials{position:absolute;left:914px;top:111px;display:flex;gap:9px}
.footer .socials span{width:37px;height:37px;border-radius:50%;border:1.5px solid var(--white)}
.footer .copy{position:absolute;left:0;width:1200px;top:320px;text-align:center;font-size:13px;color:var(--white)}
</style>
</head>
<body>

<header class="site-header">
  <div class="wordmark">HELMORA</div>
  <nav class="main-nav">
    <span class="active">Home</span><span>About us</span><span>Product</span><span>Mission</span><span>Team</span><span>Contact us</span>
  </nav>
  <div class="quote-btn">REQUEST A QUOTE</div>
</header>

<section class="hero" role="img" aria-label="Soccer player leaping to strike a ball in a floodlit stadium at dusk">
  <h1 class="hero-title">HELMORA – BRINGING SAFETY<br>TO THE SPORTS<br>CONCUSSION DEBATE</h1>
  <svg class="hero-arrow" style="left:43px" width="28" height="52" viewBox="0 0 28 52"><polyline points="25,2 3,26 25,50" fill="none" stroke="#fff" stroke-width="3"/></svg>
  <svg class="hero-arrow" style="left:1122px" width="28" height="52" viewBox="0 0 28 52"><polyline points="3,2 25,26 3,50" fill="none" stroke="#fff" stroke-width="3"/></svg>
  <div class="scroll-cue">Scroll to Discover</div>
</section>
<div class="scroll-line"></div>

<section class="about">
  <div class="frame-top-l"></div><div class="frame-top-r"></div>
  <div class="frame-l"></div><div class="frame-r"></div>
  <div class="frame-bot-l"></div><div class="frame-bot-r"></div>
  <h2>ABOUT <span>HELMORA</span></h2>
  <p>Lorem ipsum dolor sit amet, consectetur adipiscing elit, sed do eiusmod tempor incididunt ut labore et dolore magna aliqua. Ut enim ad minim veniam, quis nostrud exercitation ullamco laboris nisi ut aliquip ex ea commodo consequat. Duis aute irure dolor in reprehenderit in voluptate velit esse cillum dolore eu fugiat nulla pariatur. Excepteur sint occaecat cupidatat non proident, sunt in culpa qui officia deserunt mollit anim id est laborum.</p>
</section>
<div class="btn btn-read">READ MORE
  <svg width="13" height="13" viewBox="0 0 13 13"><circle cx="6.5" cy="6.5" r="6.5" fill="#fff"/><polyline points="5,3.5 8,6.5 5,9.5" fill="none" stroke="#0f5a9a" stroke-width="1.8"/></svg>
</div>

<section class="mission panel">
  <svg class="abs" style="left:111px;top:68px" width="40" height="40" viewBox="0 0 40 40" fill="none" stroke="#fff" stroke-width="2"><circle cx="19" cy="21" r="17"/><circle cx="19" cy="21" r="11"/><circle cx="19" cy="21" r="5"/><line x1="19" y1="21" x2="37" y2="3"/><polyline points="31,3 37,3 37,9"/></svg>
  <h3 style="left:161px;top:64px">OUR MISSION</h3>
  <h4 style="left:110px;top:123px;width:420px">HELMORA – BRINGING SAFETY TO THE SPORTS CONCUSSION DEBATE</h4>
  <p style="left:110px;top:189px;width:438px">Helmora is designing and developing head protection products to reduce the likelihood of concussion when playing sports. Exploring and understanding medical insights, material science and composites research, current and former players experiences and governing bodies guidelines has allowed Helmora to develop the safety, style, form and function requirements of a suitable product to bring to market in Q4 2020.</p>
</section>

<section class="market panel">
  <svg class="abs" style="left:55px;top:60px" width="50" height="52" viewBox="0 0 50 52" fill="none" stroke="#fff" stroke-width="2"><polyline points="2,2 2,50 48,50"/><rect x="9" y="36" width="6" height="10"/><rect x="19" y="30" width="6" height="16"/><rect x="29" y="24" width="6" height="22"/><rect x="39" y="16" width="6" height="30"/><polyline points="8,28 20,18 28,22 44,6"/></svg>
  <h3 style="left:122px;top:64px">THE MARKET TODAY</h3>
  <h4 style="left:52px;top:123px;width:420px">THERE IS A POTENTIAL £1BN MARKET IN THE UK ALONE</h4>
  <p style="left:52px;top:189px;width:436px">Soccer has no head protection product despite recent high profile head injuries, concern over the long term damage of heading the ball and greater damage of concussion in women. There are in excess of 11m people actively playing football in the UK alone (8m men, 3m women). There is no product that exists for netball, field hockey and lacrosse, as further example of the market potential of our product.</p>
</section>

<h2 class="section-title" style="top:1650px">OUR TARGETS ARE</h2>
<svg class="t-arrow" style="left:43px" width="28" height="52" viewBox="0 0 28 52"><polyline points="25,2 3,26 25,50" fill="none" stroke="#222" stroke-width="3"/></svg>
<svg class="t-arrow" style="left:1130px" width="28" height="52" viewBox="0 0 28 52"><polyline points="3,2 25,26 3,50" fill="none" stroke="#222" stroke-width="3"/></svg>

<article class="target" style="left:110px">
  <div class="photo" role="img" aria-label="Young boy holding a football above his head in front of a goal" style="background:linear-gradient(180deg,#b8c9a0,#3d5fa8 70%,#6b8f3a)"></div>
  <h5>Youth Soccer Players</h5><div class="bar"></div>
  <p>Lorem ipsum dolor sit amet, consectetur adipiscing elit</p>
</article>
<article class="target" style="left:446px">
  <div class="photo" role="img" aria-label="Father and son heading a football together in a park" style="background:linear-gradient(180deg,#5f8a3a,#8fae5c 60%,#4d7a2e)"></div>
  <h5>Parents in the UK</h5><div class="bar"></div>
  <p>Lorem ipsum dolor sit amet, consectetur adipiscing elit</p>
</article>
<article class="target" style="left:779px">
  <div class="photo" role="img" aria-label="Club players contesting a header during a match" style="background:linear-gradient(180deg,#9aa39a,#5a5f82 55%,#3f6a2e)"></div>
  <h5>Soccer Clubs</h5><div class="bar"></div>
  <p>Lorem ipsum dolor sit amet, consectetur adipiscing elit</p>
</article>

<section class="product" role="region" aria-label="Our product">
  <h3>OUR PRODUCT</h3>
  <h4>A technology breakthrough in the sport that will protect as well as allow for new data collection and analytics.</h4>
  <p>Our initial product will be simplistic in function and design to ensure we get to market in 2020. Further versions of the product will incorporate data tracking technologies to enhance analytical streams available to players and clubs. Starting with soccer, followed by other markets such as netball and field hockey, where the same issues exist today. We will create a new sector of sports apparel that will serve all communities of sport and allow for new categories of sponsorship and branding.</p>
  <div class="shot"><div class="art" role="img" aria-label="Illustration of the grey protective sports headband"></div></div>
</section>

<h2 class="section-title" style="top:2832px">OUR TEAM</h2>
<article class="member" style="left:128px">
  <div class="avatar" role="img" aria-label="Portrait of Martin Oakley" style="background:radial-gradient(circle,#d8b8a0,#b33a3a)"></div>
  <h5>MARTIN OAKLEY</h5><div class="role">Founder / CEO</div>
  <p>Martin has a wealth of experience of growing start-ups and exiting businesses, from professional services to technology companies, in recent years Martin has been an executive advisor to many global sporting talents, football clubs, right holders and other sports companies.</p>
</article>
<article class="member" style="left:452px">
  <div class="avatar" role="img" aria-label="Portrait of Rachel Dunmore" style="background:radial-gradient(circle,#e0c0aa,#4a4640)"></div>
  <h5>RACHEL DUNMORE</h5><div class="role">Co –Founder / COO</div>
  <p>Rachel has been planning and delivering commercial, large scale transformation projects within people based, high-profile and global environments for the last 15 years. COO to a former UK Prime Minister, transforming his business globally across 30 legal jurisdiction</p>
</article>
<article class="member" style="left:777px">
  <div class="avatar" role="img" aria-label="Portrait of Graham Ferris" style="background:radial-gradient(circle,#d9b49a,#c9c9c2)"></div>
  <h5>GRAHAM FERRIS</h5><div class="role">CCO</div>
  <p>Graham started his career in retail banking, later experience in corporate and private banking. Since leaving the corporate world in 2007, Graham has been bringing people and companies together in enable funding and development of projects</p>
</article>

<footer class="footer">
  <div class="f-mark">HELMORA</div>
  <p class="f-about">Lorem ipsum dolor sit amet, consec tetur adipiscing elit, sed do eiusmod tempor incididunt ut labore et dolore magna aliqua.</p>
  <h6 style="left:442px">Sitemap</h6>
  <ul style="left:443px"><li>Home</li><li>About</li><li>Product</li><li>About Coaching</li><li>Who We Can Help</li><li>Contact</li></ul>
  <h6 style="left:658px">Contact info</h6>
  <div class="contact">123, Lorem ipsum dolor sit amet<br><br>+1 888 888 8888<br><br>hello@helmora.co</div>
  <h6 style="left:915px">Social with us</h6>
  <div class="socials"><span></span><span></span><span></span><span></span></div>
  <div class="copy">© Copyrights 2020 Helmora | All Rights Reserved</div>
</footer>

</body>
</html>
```